Local Roofing/Construction company business needs new biz card design

We need a new business card design, current cards are from the start of this operation and generic at best. We are a local Construction Company (General Contractor) with a majority of our work originating from insurance claims-exterior finish work is the main focus (Roofs-Siding-Gutters etc). Heavily involved with homeowners and the low ball offers they receive from insurance company's after a insurable event takes place. I have attached some of our original logo file(s) below.

```html
<!DOCTYPE html>
<html lang="en">
<head>
<meta charset="utf-8">
<title>Stonebridge Construction – Business Card</title>
<link href="https://fonts.googleapis.com/css2?family=Montserrat:wght@400;500;700;800&display=swap" rel="stylesheet">
<style>
  :root {
    --green: #3fb65a;
    --green-soft: #4cbf66;
    --green-deep: #2f9e48;
    --ink: #1c1f1e;
    --swoosh: #14211c;
    --paper: #f8f5f2;
    --white: #ffffff;
    --stage: #e6e7e9;
  }
  * { box-sizing: border-box; margin: 0; padding: 0; }
  html, body {
    width: 1200px; height: 900px; overflow: hidden;
    background: var(--stage);
    font-family: "Montserrat", sans-serif;
  }
  .canvas {
    width: 1200px; height: 900px;
    display: flex; flex-direction: column; align-items: center; justify-content: center;
    gap: 40px;
  }
  .card {
    position: relative;
    width: 700px; height: 400px;
    border-radius: 26px;
    overflow: hidden;
    box-shadow: 0 10px 30px rgba(0,0,0,.18);
  }

  /* Back side */
  .card-back { background: var(--green); }
  .card-back .pattern-area {
    position: absolute; inset: 0;
    background: linear-gradient(135deg, var(--green-soft), var(--green) 60%, var(--green-deep));
  }
  .brand-badge {
    position: absolute; left: 50%; top: 50%;
    transform: translate(-50%, -50%);
    width: 150px; height: 110px;
    background: var(--white);
    border-radius: 18px;
    display: flex; align-items: center; justify-content: center;
    text-align: center;
    padding: 10px;
  }
  .brand-badge .brand-name {
    font-weight: 800; font-size: 15px; line-height: 1.15;
    color: var(--green); letter-spacing: .02em; text-transform: uppercase;
  }

  /* Front side */
  .card-front { background: var(--paper); }
  .card-front svg.shape { position: absolute; inset: 0; }
  .front-brand {
    position: absolute; left: 70px; top: 150px;
    display: flex; align-items: center; gap: 14px;
  }
  .front-brand .brand-mark {
    width: 46px; height: 46px; background: var(--green); border-radius: 4px;
  }
  .front-brand .brand-name {
    font-weight: 800; font-size: 26px; line-height: 1.05;
    color: var(--ink); text-transform: uppercase; letter-spacing: .01em;
  }
  .contact-block {
    position: absolute; right: 40px; top: 70px;
    text-align: right; color: var(--white);
  }
  .person-name { font-weight: 700; font-size: 27px; line-height: 1.1; }
  .person-role { font-weight: 400; font-size: 15px; margin-bottom: 16px; }
  .contact-list { list-style: none; }
  .contact-list li {
    display: flex; justify-content: flex-end; align-items: center; gap: 10px;
    font-size: 15px; line-height: 28px; font-weight: 400;
  }
  .contact-list svg { width: 14px; height: 14px; fill: var(--white); flex: none; }
</style>
</head>
<body>
<main class="canvas">

  <section class="card card-back" aria-label="Card back">
    <div class="pattern-area" role="img" aria-label="Repeating brand pattern in green tones"></div>
    <div class="brand-badge"><span class="brand-name">Stonebridge Construction</span></div>
  </section>

  <section class="card card-front" aria-label="Card front">
    <svg class="shape" viewBox="0 0 700 400" width="700" height="400" aria-hidden="true">
      <path d="M418,0 C378,210 300,372 100,400 L140,400 C330,374 406,210 446,0 Z" fill="var(--swoosh)"/>
      <path d="M440,0 C402,210 326,372 140,400 L700,400 L700,0 Z" fill="var(--green)"/>
      <path d="M436,0 C398,210 322,372 134,400" fill="none" stroke="var(--white)" stroke-width="2"/>
    </svg>

    <div class="front-brand">
      <span class="brand-mark"></span>
      <span class="brand-name">Stonebridge<br>Construction</span>
    </div>

    <div class="contact-block">
      <p class="person-name">Daniel Arlen</p>
      <p class="person-role">Managing Director</p>
      <ul class="contact-list">
        <li>555-014-2760
          <svg viewBox="0 0 24 24"><path d="M6.6 10.8a15 15 0 0 0 6.6 6.6l2.2-2.2a1 1 0 0 1 1-.25 11.4 11.4 0 0 0 3.6.57 1 1 0 0 1 1 1V20a1 1 0 0 1-1 1A17 17 0 0 1 3 4a1 1 0 0 1 1-1h3.5a1 1 0 0 1 1 1c0 1.25.2 2.45.57 3.57a1 1 0 0 1-.25 1z"/></svg>
        </li>
        <li>555-014-2760
          <svg viewBox="0 0 24 24"><path d="M7 1h10a2 2 0 0 1 2 2v18a2 2 0 0 1-2 2H7a2 2 0 0 1-2-2V3a2 2 0 0 1 2-2zm0 3v15h10V4z"/></svg>
        </li>
        <li>info@stonebridgebuild.com
          <svg viewBox="0 0 24 24"><path d="M2 5h20v14H2zm2 2v.5l8 5 8-5V7z"/></svg>
        </li>
        <li>www.stonebridgebuild.com
          <svg viewBox="0 0 24 24"><path d="M12 2a10 10 0 1 0 0 20 10 10 0 0 0 0-20zm0 2c1 0 2.3 2.2 2.7 6H9.3C9.7 6.2 11 4 12 4zm-7.9 8h3.2c.1 2 .5 3.8 1.1 5.2A8 8 0 0 1 4.1 12zm11.6 5.2c.6-1.4 1-3.2 1.1-5.2h3.2a8 8 0 0 1-4.3 5.2z"/></svg>
        </li>
      </ul>
    </div>
  </section>

</main>
</body>
</html>
```